Folded A4 flyer for design&construction company

Folded A4 flyer needed. Keywords: elegant, stylish
our website www.dorvika.ae

Industry/Entity Type

Construction

```html
<!DOCTYPE html>
<html lang="en">
<head>
<meta charset="utf-8">
<title>Dorvika – Folded A4 Flyer</title>
<link href="https://fonts.googleapis.com/css2?family=Montserrat:wght@400&family=Open+Sans:wght@400;600;700&family=Courgette&display=swap" rel="stylesheet">
<style>
  :root {
    --backdrop: #5b675a;
    --paper: #ffffff;
    --paper-cool: #eeeef3;
    --ink: #1d1d1f;
    --ink-soft: #3a3a3c;
    --gold: #c9a24a;
    --gold-deep: #8e6f2e;
    --gold-light: #f0d27a;
    --silver: #b9bac0;
    --photo-warm: #d39a2a;
    --photo-floor: #c28a3c;
    --photo-wall: #e8e2d8;
  }
  * { box-sizing: border-box; margin: 0; padding: 0; }
  html, body { width: 1200px; height: 789px; overflow: hidden; }
  body { background: var(--backdrop); font-family: "Open Sans", sans-serif; color: var(--ink); }

  .spread { position: absolute; left: 180px; top: 97px; width: 840px; height: 594px; display: flex; box-shadow: 0 14px 30px rgba(0,0,0,.35); }
  .page { position: relative; width: 420px; height: 594px; overflow: hidden; }
  .page--back { background: linear-gradient(160deg, var(--paper) 0%, var(--paper-cool) 100%); }
  .page--front { background: var(--paper); }

  .wordmark { font-family: "Montserrat", sans-serif; font-weight: 400; color: var(--ink); letter-spacing: 1px; line-height: 1; }
  .tagline { font-family: "Courgette", cursive; color: var(--gold); }
  .ornament { background: linear-gradient(90deg, transparent, var(--gold-light), var(--gold), var(--gold-light), transparent); border-radius: 50%; }

  /* front */
  .front-brand { position: absolute; top: 30px; left: 0; right: 0; text-align: center; }
  .front-brand .ornament { width: 150px; height: 34px; margin: 0 auto 6px; }
  .front-brand .wordmark { font-size: 50px; }
  .front-brand .tagline { font-size: 15px; margin-top: 2px; }
  .front-photo { position: absolute; top: 160px; left: 0; width: 420px; height: 270px;
    background: linear-gradient(180deg, var(--photo-wall) 0%, var(--photo-warm) 40%, var(--photo-floor) 75%, #a8732f 100%); }
  .quote { position: absolute; top: 398px; left: 0; right: 0; text-align: center; font-family: "Courgette", cursive; color: #fff; font-size: 15px; text-shadow: 0 1px 2px rgba(0,0,0,.4); }
  .web-band { position: absolute; left: 20px; right: 20px; height: 28px; display: flex; align-items: center; justify-content: center;
    background: linear-gradient(90deg, transparent 0%, var(--gold-deep) 30%, var(--gold) 60%, transparent 100%);
    color: #fff; font-weight: 600; font-size: 14px; letter-spacing: .5px; }
  .page--front .web-band { top: 470px; }

  /* back */
  .back-brand { position: absolute; top: 46px; left: 0; right: 0; text-align: center; }
  .back-brand .ornament { width: 90px; height: 20px; margin: 0 auto 3px; }
  .back-brand .wordmark { font-size: 32px; }
  .back-brand .tagline { font-size: 10px; }
  .about { position: absolute; top: 150px; left: 62px; right: 62px; font-size: 11.5px; line-height: 1.42; text-align: justify; color: var(--ink-soft); }
  .back-ornament { position: absolute; top: 272px; left: 110px; width: 200px; height: 60px; opacity: .55;
    background: radial-gradient(ellipse at center, var(--silver) 0%, transparent 70%); }
  .contact { position: absolute; top: 350px; left: 0; right: 0; }
  .quote-badge { position: absolute; left: 78px; top: 0; width: 96px; height: 96px; }
  .phone { position: absolute; left: 196px; top: 26px; font-size: 19px; color: var(--ink); }
  .or-pill { position: absolute; left: 230px; top: 60px; width: 38px; height: 18px; border-radius: 9px; background: var(--silver); color: #fff; font-size: 12px; text-align: center; line-height: 18px; }
  .email { position: absolute; left: 0; right: 0; top: 88px; text-align: center; font-size: 15px; }
  .page--back .web-band { top: 468px; }
  .address { position: absolute; top: 530px; left: 0; right: 0; text-align: center; font-size: 10.5px; color: var(--ink-soft); }
</style>
</head>
<body>
<main class="spread">
  <section class="page page--back">
    <header class="back-brand">
      <div class="ornament" role="img" aria-label="Gold filigree crown ornament"></div>
      <div class="wordmark">DORVIKA</div>
      <div class="tagline">design &amp; construction</div>
    </header>
    <p class="about">We believe in quality beginnings and flawless finishes. We are a team of creative designers and constructors with years of experience and expertise in providing complete interior design and construction services. Our unique designing prowess is complemented by our unflinching commitment to quality construction. Our team specializes in classic and contemporary high quality construction in Dubai for commercial and residential projects.</p>
    <div class="back-ornament" role="img" aria-label="Faint silver scroll ornament"></div>
    <div class="contact">
      <svg class="quote-badge" viewBox="0 0 96 96" aria-label="Get a free quote today">
        <circle cx="48" cy="48" r="46" fill="#e4e4e8"/>
        <circle cx="48" cy="48" r="40" fill="#e0ad26"/>
        <g transform="rotate(-22 48 48)" font-family="Open Sans, sans-serif" text-anchor="middle" fill="#1d1d1f">
          <text x="48" y="38" font-size="10" font-weight="600">GET A</text>
          <text x="48" y="54" font-size="14" font-weight="700">FREE QUOTE</text>
          <text x="48" y="67" font-size="10" font-weight="600">TODAY</text>
        </g>
      </svg>
      <div class="phone">800-DORVIKA</div>
      <div class="or-pill">or</div>
      <div class="email">CONTACT@DORVIKA.AE</div>
    </div>
    <div class="web-band">WWW.DORVIKA.AE</div>
    <p class="address">Dorvika LLC, Harbor Crest Building, Office 1207, Business Bay, Dubai</p>
  </section>

  <section class="page page--front">
    <header class="front-brand">
      <div class="ornament" role="img" aria-label="Gold filigree crown ornament"></div>
      <div class="wordmark">DORVIKA</div>
      <div class="tagline">design &amp; construction</div>
    </header>
    <div class="front-photo" role="img" aria-label="Photo of a modern interior with a curved white staircase, orange ceiling and golden parquet floor"></div>
    <p class="quote">Quality is not an act, it is a habit - Old Proverb</p>
    <div class="web-band">WWW.DORVIKA.AE</div>
  </section>
</main>
</body>
</html>
```